Letterhead and matching envelope design for a dental office

We need a new stationary design, letterhead and envelope #10, for a dental office in Denver area. We are called Bright Harbor Dental. We want a simple and minimalistic design but not a boring design. I wish to have one good point that makes it look professional. I have attached our logo. Feel free to use either one. I want the design for letterhead and envelope look like a "matching pair" but not look the same. The envelope doesn't have to be white and it will have an address window on bottom left.

Target Market(s)

everyone who visits dentist (adults)

Industry/Entity Type

Dental

Font styles to use
Other font styles liked:
• close to font on logo or something that matches well

Requirements
Must have
• professional
• simple, minimalistic
• unique point that stands out
Nice to have
• matching but not same design for letterhead and envelope
Should not have
• not look like all the other boring designs
• no flowery, distracting feats

```html
<!DOCTYPE html>
<html lang="en">
<head>
<meta charset="utf-8">
<title>Bright Harbor Dental – Letterhead and Envelope</title>
<link rel="stylesheet" href="https://fonts.googleapis.com/css2?family=Source+Sans+3:wght@400;600;700&display=swap">
<style>
  :root {
    --brand-green: #3ab54a;
    --brand-green-light: #a8dcae;
    --leaf-tint: #e6f2e3;
    --leaf-tint-deep: #d7ead3;
    --ink: #333333;
    --ink-soft: #6a6a6a;
    --paper: #ffffff;
    --backdrop: #e8e8e8;
  }
  * { margin: 0; padding: 0; box-sizing: border-box; }
  html, body {
    width: 1200px; height: 799px; overflow: hidden;
    background: var(--backdrop);
    font-family: "Source Sans 3", "Myriad Pro", Arial, sans-serif;
    color: var(--ink);
  }
  .stationery { position: relative; width: 1200px; height: 799px; }

  /* ---------- Letterhead ---------- */
  .letterhead {
    position: absolute; left: 60px; top: 70px;
    width: 500px; height: 647px;
    background: var(--paper);
    box-shadow: 0 2px 6px rgba(0,0,0,.12);
    overflow: hidden;
  }
  .brand-mark {
    display: flex; align-items: center; gap: 7px;
    color: var(--brand-green);
    font-weight: 600; letter-spacing: 2px; text-transform: uppercase;
  }
  .brand-mark__dot {
    width: 10px; height: 10px; border-radius: 50%;
    background: var(--brand-green);
  }
  .letterhead .brand-mark { position: absolute; top: 38px; right: 40px; font-size: 13px; }

  .letter-body { position: absolute; left: 48px; top: 110px; width: 380px; }
  .letter-body__greeting { font-size: 12px; font-weight: 700; margin-bottom: 10px; }
  .letter-body p { font-size: 8.5px; line-height: 1.45; color: var(--ink-soft); margin-bottom: 9px; }
  .signature {
    width: 90px; height: 28px; margin-top: 14px;
    background: linear-gradient(90deg, #d9d9d9, #bdbdbd);
    border-radius: 14px;
  }

  .leaf-art {
    position: absolute;
    background: radial-gradient(ellipse at 40% 50%, var(--leaf-tint-deep), var(--leaf-tint) 65%, rgba(230,242,227,0) 100%);
  }
  .letterhead .leaf-art { left: 100px; top: 360px; width: 360px; height: 230px; }

  .contact { position: absolute; left: 48px; top: 470px; font-size: 10px; line-height: 1.45; }
  .contact__name { color: var(--brand-green); }
  .contact__lines { margin-top: 2px; }
  .contact__links { position: absolute; left: 178px; top: 500px; font-size: 10px; line-height: 1.6; }
  .contact__row { display: flex; align-items: center; gap: 5px; }
  .contact__icon { width: 11px; height: 11px; }

  .footer-band {
    position: absolute; left: 0; right: 0; bottom: 14px; height: 5px;
    background: var(--brand-green-light);
  }
  .footer-tab {
    position: absolute; right: 0; bottom: 12px;
    width: 180px; height: 22px;
    background: var(--brand-green);
    clip-path: polygon(10px 0, 100% 0, 100% 100%, 0 100%);
    color: #fff; font-size: 10px;
    display: flex; align-items: center; justify-content: center;
  }

  /* ---------- Envelope back ---------- */
  .envelope-back {
    position: absolute; left: 600px; top: 90px;
    width: 560px; height: 244px;
    background: var(--paper);
    box-shadow: 0 2px 6px rgba(0,0,0,.12);
    overflow: hidden;
  }
  .envelope-back__flap { position: absolute; inset: 0; }
  .envelope-back .brand-mark {
    position: absolute; left: 312px; top: 82px;
    color: #fff; font-size: 11px;
  }
  .envelope-back .brand-mark__dot { background: #fff; width: 8px; height: 8px; }

  /* ---------- Envelope front ---------- */
  .envelope-front {
    position: absolute; left: 600px; top: 400px;
    width: 560px; height: 244px;
    background: var(--paper);
    box-shadow: 0 2px 6px rgba(0,0,0,.12);
    overflow: hidden;
  }
  .envelope-front .brand-mark { position: absolute; left: 36px; top: 34px; font-size: 13px; }
  .envelope-front .contact { left: 36px; top: 118px; }
  .envelope-front .leaf-art { left: 260px; top: 80px; width: 300px; height: 160px; }
</style>
</head>
<body>
<main class="stationery">

  <section class="letterhead" aria-label="Letterhead">
    <div class="brand-mark"><span class="brand-mark__dot"></span>Bright Harbor Dental</div>

    <div class="letter-body">
      <p class="letter-body__greeting">Dear Mr. Carter,</p>
      <p>We are glad to welcome you to our practice. This letter shares a short note about your next visit, the care plan we discussed and the times our front desk is open for questions.</p>
      <p>Please bring your insurance card and a list of current medicines. If you need to change the time, call us one day ahead and we will find a new slot that suits you.</p>
      <p>Thank you for trusting our team with your smile. We look forward to seeing you soon and to keeping your teeth healthy for many years.</p>
      <div class="signature" role="img" aria-label="Handwritten signature"></div>
    </div>

    <div class="leaf-art" role="img" aria-label="Two large pale green leaves on a stem"></div>

    <div class="contact">
      <div class="contact__name">Bright Harbor Dental</div>
      <div class="contact__lines">4820 Lakeview Ave,<br>Suite 210 Arvada, CO 80002</div>
    </div>
    <div class="contact__links">
      <div class="contact__row">
        <svg class="contact__icon" viewBox="0 0 12 12" aria-hidden="true"><circle cx="6" cy="6" r="6" fill="#3ab54a"/><path d="M4 3.2l1 1.3-.6.8a4 4 0 0 0 2.3 2.3l.8-.6 1.3 1-.6 1a5.5 5.5 0 0 1-5.2-5.2z" fill="#fff"/></svg>
        303-555-0147
      </div>
      <div class="contact__row">
        <svg class="contact__icon" viewBox="0 0 12 12" aria-hidden="true"><circle cx="6" cy="6" r="6" fill="#3ab54a"/><rect x="3" y="4" width="6" height="4.2" fill="#fff"/><path d="M3 4l3 2.3L9 4" fill="none" stroke="#3ab54a" stroke-width=".7"/></svg>
        info@brightharbordental.com
      </div>
    </div>

    <div class="footer-band"></div>
    <div class="footer-tab">www.brightharbordental.com</div>
  </section>

  <section class="envelope-back" aria-label="Envelope back">
    <svg class="envelope-back__flap" viewBox="0 0 560 244" preserveAspectRatio="none" aria-hidden="true">
      <path d="M0 0 H560 V150 Q555 175 525 178 L300 178 Q285 176 270 165 L0 0 Z" fill="#3ab54a"/>
    </svg>
    <div class="brand-mark"><span class="brand-mark__dot"></span>Bright Harbor Dental</div>
  </section>

  <section class="envelope-front" aria-label="Envelope front">
    <div class="brand-mark"><span class="brand-mark__dot"></span>Bright Harbor Dental</div>
    <div class="contact">
      <div class="contact__name">Bright Harbor Dental</div>
      <div class="contact__lines">4820 Lakeview Ave, Suite 210 Arvada, CO 80002</div>
    </div>
    <div class="leaf-art" role="img" aria-label="Two large pale green leaves on a stem"></div>
    <div class="footer-band"></div>
    <div class="footer-tab">www.brightharbordental.com</div>
  </section>

</main>
</body>
</html>
```